Company director needs a business card design

I am a semi-retired former senior finance executive who sits on a number of public and private company boards and do some consulting work. I work largely with emerging businesses but deal regularly with top end of town lawyers, bankers etc. I need a thoughtful but relatively conservative design which would also resonate with my younger client base. Some colour would be good. Information limited to name, address, office tel, mobile and email.

Finance

```html
<!DOCTYPE html>
<html lang="en">
<head>
<meta charset="utf-8">
<title>Business Card – Hollis Grant</title>
<link rel="stylesheet" href="https://fonts.googleapis.com/css2?family=Exo+2:wght@400;600&family=Open+Sans:wght@600&display=swap">
<style>
  :root {
    --page-bg: #d9d6cf;
    --card-bg: #ece9e2;
    --card-shadow: rgba(40, 32, 20, 0.22);
    --ink: #1e1e1e;
    --ink-soft: #2b2b2b;
  }
  * { margin: 0; padding: 0; box-sizing: border-box; }
  html, body {
    width: 1200px;
    height: 800px;
    overflow: hidden;
    background: var(--page-bg);
  }
  .canvas {
    position: relative;
    width: 1200px;
    height: 800px;
  }
  .card {
    position: absolute;
    left: 180px;
    top: 160px;
    width: 840px;
    height: 480px;
    background: var(--card-bg);
    box-shadow: 0 10px 30px var(--card-shadow);
    font-family: "Exo 2", sans-serif;
    color: var(--ink);
  }
  .contact-list {
    position: absolute;
    left: 56px;
    top: 46px;
    list-style: none;
  }
  .contact-item {
    display: flex;
    align-items: center;
    height: 32px;
    font-size: 20px;
    letter-spacing: 0.06em;
    white-space: nowrap;
  }
  .contact-icon {
    width: 20px;
    height: 20px;
    margin-right: 20px;
    flex: none;
  }
  .address {
    position: absolute;
    left: 56px;
    top: 200px;
    font-size: 20px;
    line-height: 25px;
    letter-spacing: 0.08em;
    color: var(--ink-soft);
    white-space: nowrap;
  }
  .identity {
    position: absolute;
    right: 96px;
    top: 268px;
    text-align: right;
  }
  .identity-name {
    font-family: "Exo 2", sans-serif;
    font-weight: 600;
    font-size: 30px;
    letter-spacing: 0.07em;
    line-height: 1;
    white-space: nowrap;
  }
  .identity-title {
    font-family: "Open Sans", sans-serif;
    font-weight: 600;
    font-size: 13px;
    margin-top: 3px;
  }
</style>
</head>
<body>
<main class="canvas">
  <section class="card" aria-label="Business card">
    <ul class="contact-list">
      <li class="contact-item">
        <svg class="contact-icon" viewBox="0 0 20 20" aria-hidden="true">
          <rect x="4" y="2" width="12" height="16" rx="2" fill="none" stroke="currentColor" stroke-width="2"/>
          <line x1="8" y1="15" x2="12" y2="15" stroke="currentColor" stroke-width="1.5"/>
        </svg>
        <span>0045 7781 203</span>
      </li>
      <li class="contact-item">
        <svg class="contact-icon" viewBox="0 0 20 20" aria-hidden="true">
          <rect x="4" y="2" width="12" height="17" fill="currentColor"/>
          <rect x="7" y="5" width="2" height="2" fill="#ece9e2"/>
          <rect x="11" y="5" width="2" height="2" fill="#ece9e2"/>
          <rect x="7" y="9" width="2" height="2" fill="#ece9e2"/>
          <rect x="11" y="9" width="2" height="2" fill="#ece9e2"/>
          <rect x="7" y="13" width="2" height="2" fill="#ece9e2"/>
          <rect x="11" y="13" width="2" height="2" fill="#ece9e2"/>
          <rect x="2" y="18" width="16" height="1.5" fill="currentColor"/>
        </svg>
        <span>0045 7781 240</span>
      </li>
      <li class="contact-item">
        <svg class="contact-icon" viewBox="0 0 20 20" aria-hidden="true">
          <rect x="1" y="4" width="18" height="12" fill="currentColor"/>
          <polyline points="1.5,4.5 10,11 18.5,4.5" fill="none" stroke="#ece9e2" stroke-width="1.3"/>
          <line x1="1.5" y1="15.5" x2="8" y2="9.5" stroke="#ece9e2" stroke-width="1.1"/>
          <line x1="18.5" y1="15.5" x2="12" y2="9.5" stroke="#ece9e2" stroke-width="1.1"/>
        </svg>
        <span>office@hollisgrant.com</span>
      </li>
      <li class="contact-item">
        <svg class="contact-icon" viewBox="0 0 20 20" aria-hidden="true">
          <rect x="1.5" y="3" width="17" height="11" rx="1" fill="none" stroke="currentColor" stroke-width="2"/>
          <rect x="8" y="14" width="4" height="3" fill="currentColor"/>
          <rect x="5" y="17" width="10" height="1.8" fill="currentColor"/>
        </svg>
        <span>www.hollisgrant.com</span>
      </li>
    </ul>

    <p class="address">Grant Advisory 14 Elm Street<br>Larkfield, NJ 07990</p>

    <div class="identity">
      <h1 class="identity-name">HOLLIS GRANT</h1>
      <p class="identity-title">Managing Director</p>
    </div>
  </section>
</main>
</body>
</html>
```